Etikett für Rotweinflasche
Liebe farbkosmos Atelier, wir werden uns bei der endgültigen Etikettengestaltung (finale Größe + Rückseite) noch an Euch melden. Bitte sendet uns euren Kontakt an helga.brandt@morvelli.wine
Zielgruppe
Morvelli Italia ist ein exklusives Boutique-Weingut in Sizilien, das hochqualitative Spitzenweine in kleinen Mengen mit modernster Technologie und stets nachhaltig erzeugt. Wir hinterfragen sowohl in der Agronomie im Weingarten als auch in der Önologie im Weinkeller alle herrschenden Traditionen und trachten danach, stets das beste Endprodukt zu kreieren. Der vulkanische, kalkreiche Boden Siziliens sowie trockene, sonnenreiche und niederschlagsarme Vegetationsperioden sind unsere optimale Basis.
Zielgruppe: Internationale Genussmenschen jeglichen Alters, die sich bewusst auch höherpreisige Weine (um die €30+) gönnen , vor allem kunstaffine young professionals mit Qualitäts-& Nachhaltigkeitsanspruch
Aufgabenstellung
Das Etikett ist für Rotwein-Flaschen (Cabernet Sauvignon / Nero D'Avola / Frappato / Syrah / Cerasuolo / Petit Verdot / sowie einen Bourdeaux-Cuveè aus Cabernet Sauvignon und Petit Verdot) .
Die Flasche ist reinschwarz, sehr hochwertig und schwer.
Flaschenform: Bordeauxflasche siehe technisches Datenblatt
Sleeve über dem Korken: schwarz mit weißer Schrift wie bisher
Zu gestalten ist das Etikett der Vorderseite. Zumindest die jeweilige Rotwein-Sorte ist auch textlich darzustellen (zwecks Scannen mit Trubel-App)
Der Kreativität kann freien Lauf gelassen werden! Unterscheidbarkeit vom Markt ist explizit gewollt.
Unsere aktuellen Etiketten und Markenauftritt siehe: https://morvelli.wine/shop/

```html
<!DOCTYPE html>
<html lang="en">
<head>
<meta charset="utf-8">
<title>Morvelli Cabernet Sauvignon – Bottle with Front Label</title>
<link rel="stylesheet" href="https://fonts.googleapis.com/css2?family=Cormorant+Garamond:wght@500&family=Montserrat:wght@500&display=swap">
<style>
  :root {
    --canvas-bg: #ffffff;
    --glass-deep: #050304;
    --glass-wine: #3a0e14;
    --glass-shine: #6a5a5e;
    --sleeve-black: #0b0b0b;
    --sleeve-edge: #1c1c1c;
    --text-light: #f8f4f2;
    --tone-rose: #d86a78;
    --tone-coral: #e57c70;
    --tone-mist: #cfc6de;
    --tone-haze: #ece6f2;
    --tone-bark: #3b3038;
    --tone-ground: #9a8f9c;
    --reflection: #9a9a9a;
  }
  * { margin: 0; padding: 0; box-sizing: border-box; }
  html, body {
    width: 849px;
    height: 1200px;
    overflow: hidden;
    background: var(--canvas-bg);
  }
  .canvas { display: block; width: 849px; height: 1200px; }
  .brand-name {
    font-family: "Cormorant Garamond", serif;
    font-weight: 500;
    font-size: 13px;
    fill: var(--text-light);
    letter-spacing: 0.02em;
  }
  .brand-region {
    font-family: "Montserrat", sans-serif;
    font-weight: 500;
    font-size: 6px;
    fill: var(--text-light);
    letter-spacing: 0.2em;
  }
  .variety-name {
    font-family: "Cormorant Garamond", serif;
    font-weight: 500;
    font-size: 8.5px;
    letter-spacing: 0.12em;
    fill: var(--text-light);
  }
</style>
</head>
<body>
<svg class="canvas" viewBox="0 0 849 1200" xmlns="http://www.w3.org/2000/svg">
  <defs>
    <linearGradient id="glass" x1="0" x2="1" y1="0" y2="0">
      <stop offset="0" stop-color="var(--glass-deep)"/>
      <stop offset="0.12" stop-color="var(--glass-wine)"/>
      <stop offset="0.3" stop-color="var(--glass-deep)"/>
      <stop offset="0.85" stop-color="var(--glass-deep)"/>
      <stop offset="0.95" stop-color="var(--glass-shine)"/>
      <stop offset="1" stop-color="var(--glass-deep)"/>
    </linearGradient>
    <linearGradient id="sleeve" x1="0" x2="1" y1="0" y2="0">
      <stop offset="0" stop-color="var(--sleeve-black)"/>
      <stop offset="0.5" stop-color="var(--sleeve-edge)"/>
      <stop offset="1" stop-color="var(--sleeve-black)"/>
    </linearGradient>
    <linearGradient id="artwork-base" x1="0" x2="1" y1="0" y2="0">
      <stop offset="0" stop-color="var(--tone-rose)"/>
      <stop offset="0.25" stop-color="#c98a9a"/>
      <stop offset="0.45" stop-color="var(--tone-haze)"/>
      <stop offset="0.62" stop-color="var(--tone-mist)"/>
      <stop offset="0.82" stop-color="var(--tone-coral)"/>
      <stop offset="0.92" stop-color="#b8646c"/>
      <stop offset="0.96" stop-color="var(--tone-bark)"/>
      <stop offset="1" stop-color="var(--tone-bark)"/>
    </linearGradient>
    <linearGradient id="artwork-ground" x1="0" x2="0" y1="0" y2="1">
      <stop offset="0.5" stop-color="var(--tone-ground)" stop-opacity="0"/>
      <stop offset="1" stop-color="var(--tone-ground)" stop-opacity="0.8"/>
    </linearGradient>
    <radialGradient id="artwork-cloak" cx="0.68" cy="0.75" r="0.3">
      <stop offset="0" stop-color="var(--tone-coral)" stop-opacity="0.95"/>
      <stop offset="1" stop-color="var(--tone-coral)" stop-opacity="0"/>
    </radialGradient>
    <radialGradient id="artwork-gown" cx="0.42" cy="0.72" r="0.2">
      <stop offset="0" stop-color="#f8f6fb" stop-opacity="0.95"/>
      <stop offset="1" stop-color="#f8f6fb" stop-opacity="0"/>
    </radialGradient>
    <linearGradient id="floor-reflection" x1="0" x2="0" y1="0" y2="1">
      <stop offset="0" stop-color="var(--reflection)" stop-opacity="0.75"/>
      <stop offset="1" stop-color="var(--reflection)" stop-opacity="0"/>
    </linearGradient>
  </defs>

  <!-- floor reflection -->
  <path class="bottle-reflection" d="M324,1062 L538,1062 L532,1190 L330,1190 Z" fill="url(#floor-reflection)"/>

  <!-- bottle body -->
  <path class="bottle-glass" fill="url(#glass)"
        d="M386,258 L386,318 C386,362 310,378 310,440 L312,560 L321,1040 Q322,1060 342,1061 L520,1061 Q540,1060 541,1040 L550,560 L552,440 C552,378 476,362 476,318 L476,258 Z"/>

  <!-- neck sleeve -->
  <g class="neck-sleeve">
    <rect x="390" y="82" width="82" height="30" rx="6" fill="url(#sleeve)"/>
    <rect x="386" y="108" width="90" height="154" rx="3" fill="url(#sleeve)"/>
    <text class="brand-name" x="431" y="219" text-anchor="middle">MORVELLI</text>
    <text class="brand-region" x="432" y="231" text-anchor="middle">SICILIA</text>
  </g>

  <!-- front label -->
  <g class="front-label">
    <g class="label-artwork" role="img" aria-label="Dreamy pink autumn forest with a woman in a white gown and flowing coral cloak holding an owl">
      <rect x="310" y="500" width="242" height="143" fill="url(#artwork-base)"/>
      <rect x="310" y="500" width="242" height="143" fill="url(#artwork-ground)"/>
      <rect x="310" y="500" width="242" height="143" fill="url(#artwork-gown)"/>
      <rect x="310" y="500" width="242" height="143" fill="url(#artwork-cloak)"/>
    </g>
    <text class="variety-name" x="430" y="630" text-anchor="middle">CABERNET SAUVIGNON</text>
  </g>
</svg>
</body>
</html>
```